Business Card Design Project : Ridgeline Press

In preparation for market launch, Tamarind's Ridgeline Press require the development of a business card. Ridgeline Press is a Community online publishing web portal. We provide the the city of Whistler located in B.C. (Canada) business directories, News, Classified ads, News, Events and blogs etc.

The main focus of the brand is to help local businesses to corporate with their online advertisement and marketing. Meeting our clients face to face is a must (B2B).

Target Market(s)

The target market is B2B customers. Business Owners to Marketing, advertising Managers

Industry/Entity Type

Business

Requirements
Must have
• - The business card will be two sided.
the BACK side will have our logo which consist of (icon, url,slogan) submited. The logo will be middle and centred.

The FRONT side should have company details:

Company Legal Name: TAMARIND RIDGELINE MEDIA

Owen Farsk
Director of Sales & Marketing

www.tamarindridgeline.biz
owen@tamarindridgeline.biz

Phone: 604 317 8842
#2714 - 582 E. Halvern St.
Vancouver, B.C. V7K2R4 Canada
Nice to have
• - For the "FRONT" side of our business card. You can separate or re-arrange with our logo components (icon, logo,slogan). It does not have to be together.

Also our company legal name is rather long so arrange or organize the name in a way to make it shorter. Your experience and creativity will have to come in play.
Should not have
• should not have other colors beside logo color and black text (2 colors). Also nothing Three dimensional

```html
<!DOCTYPE html>
<html lang="en">
<head>
<meta charset="utf-8">
<title>Ridgeline Press — Business Card</title>
<link rel="stylesheet" href="https://fonts.googleapis.com/css2?family=Source+Sans+3:wght@400;600;700&display=swap">
<style>
  :root {
    --brand-blue: #1478c2;
    --brand-blue-deep: #0a5fa6;
    --brand-blue-light: #2a8fd6;
    --ink: #1a1a1a;
    --paper: #ffffff;
    --backdrop: #e9ebee;
  }
  * { box-sizing: border-box; margin: 0; padding: 0; }
  html, body {
    width: 1200px; height: 944px; overflow: hidden;
    background: var(--backdrop);
    font-family: "Source Sans 3", "Myriad Pro", Arial, sans-serif;
  }
  .canvas { position: relative; width: 1200px; height: 944px; }

  .card {
    position: absolute;
    width: 580px; height: 331px;
    border-radius: 22px;
    overflow: hidden;
  }

  /* Back side */
  .card--back {
    left: 80px; top: 110px;
    background: radial-gradient(ellipse at 50% 40%, var(--brand-blue-light) 0%, var(--brand-blue) 55%, var(--brand-blue-deep) 100%);
  }
  .back-lockup {
    position: absolute; left: 0; right: 0; top: 58px;
    display: flex; flex-direction: column; align-items: center;
  }
  .back-lockup__name {
    display: flex; align-items: center; gap: 14px;
    color: var(--paper); font-weight: 700; font-size: 44px;
    letter-spacing: 0.5px; height: 96px;
  }
  .back-lockup__dot {
    width: 22px; height: 22px; border-radius: 50%; background: var(--paper);
  }
  .back-lockup__url {
    margin-top: 14px;
    color: var(--ink); font-weight: 700; font-size: 33px; letter-spacing: 0.2px;
  }
  .back-lockup__slogan {
    margin-top: 0; margin-left: 120px;
    color: var(--paper); font-size: 24px; font-weight: 400;
  }

  /* Front side */
  .card--front {
    left: 540px; top: 500px;
    background: var(--paper);
    box-shadow: 0 1px 3px rgba(0,0,0,0.12);
  }
  .front-band {
    position: absolute; left: 0; right: 0; top: 112px; height: 62px;
    background: var(--brand-blue);
  }
  .front-mark {
    position: absolute; left: 40px; top: 52px;
    display: flex; align-items: center; gap: 10px;
    color: var(--brand-blue); font-weight: 700; font-size: 30px;
  }
  .front-mark__dot {
    width: 16px; height: 16px; border-radius: 50%; background: var(--brand-blue);
  }
  .front-web {
    position: absolute; right: 26px; top: 54px; text-align: right;
  }
  .front-web__url { color: var(--ink); font-weight: 700; font-size: 20px; }
  .front-web__slogan { color: var(--brand-blue); font-size: 15px; margin-top: 2px; }

  .front-person {
    position: absolute; right: 26px; top: 118px; text-align: right; color: var(--paper);
  }
  .front-person__name { font-size: 25px; font-weight: 400; line-height: 1.1; }
  .front-person__title { font-size: 15px; margin-top: 2px; }

  .front-contact {
    position: absolute; right: 26px; top: 196px; text-align: right;
    color: var(--ink); font-size: 17px; line-height: 1.35;
  }
  .front-contact__address { margin-bottom: 18px; }
  .front-contact__domain { color: var(--brand-blue); }
</style>
</head>
<body>
<main class="canvas">

  <section class="card card--back" aria-label="Business card, back side">
    <div class="back-lockup">
      <div class="back-lockup__name"><span class="back-lockup__dot"></span>Ridgeline Press</div>
      <div class="back-lockup__url">www.tamarindridgeline.biz</div>
      <div class="back-lockup__slogan">Your information gateway</div>
    </div>
  </section>

  <section class="card card--front" aria-label="Business card, front side">
    <div class="front-band"></div>
    <div class="front-mark"><span class="front-mark__dot"></span>Ridgeline Press</div>

    <div class="front-web">
      <div class="front-web__url">www.tamarindridgeline.biz</div>
      <div class="front-web__slogan">Your information gateway</div>
    </div>

    <div class="front-person">
      <div class="front-person__name">Owen Farsk</div>
      <div class="front-person__title">Director of Sales &amp; Marketing</div>
    </div>

    <address class="front-contact" style="font-style: normal;">
      <div class="front-contact__address">
        #2714 - 582 E. Halvern St.<br>
        Vancouver, B.C.V7K2R4 Canada
      </div>
      <div>604 317 8842</div>
      <div>owen@<span class="front-contact__domain">tamarindridgeline</span>.biz</div>
    </address>
  </section>

</main>
</body>
</html>
```